Landscaping flier 2024

Create a 1 page flier for landscaping services
1. Must be completed in Adobe Photoshop
2. Size 8.5" x 11" (portrait layout)
3. Include logo
4. Text to include:
2024 Gravesite Landscaping Packages
info@hollowbrookmemorial.org
(201) 555-0148
hollowbrookmemorial.org
5. Use chart text for the content. DO NOT COPY THE CHART DESIGN/FORMAT. Use the chart for the text you need only.
6. Use "Pricing cards as format for laying out the chart". Open to other ideas as well.
**Use the example of chart design (handwritten) to base your design off of.
7. Photos
-include before and after care photos

```html
<!DOCTYPE html>
<html lang="en">
<head>
<meta charset="utf-8">
<title>Hollowbrook Memorial – 2024 Gravesite Landscaping Packages</title>
<link rel="stylesheet" href="https://fonts.googleapis.com/css2?family=Poppins:wght@400;500;600;700;800&display=swap">
<style>
  :root{
    --maroon:#7a1f2a;
    --maroon-deep:#5e1418;
    --ink:#2b2b2b;
    --charcoal:#363636;
    --panel:#ececec;
    --panel-stripe:#e1e1e1;
    --pink:#f1cfd1;
    --pink-stripe:#e7bdc0;
    --check:#2fb36a;
    --cross:#e0393b;
    --page:#f2f2f2;
    --white:#ffffff;
  }
  *{margin:0;padding:0;box-sizing:border-box}
  html,body{width:1200px;height:2400px;overflow:hidden;background:var(--page)}
  body{font-family:"Poppins",sans-serif;color:var(--ink);position:relative}

  .flier{position:absolute;left:0;top:423px;width:977px;height:1265px;transform:scale(1.2282);transform-origin:0 0;background:var(--white);overflow:hidden}

  .hero-photo{position:absolute;left:0;top:0;width:977px;height:428px;
    background:
      linear-gradient(90deg,rgba(94,20,24,.95) 0%,rgba(110,26,28,.85) 35%,rgba(120,34,26,.35) 60%,rgba(0,0,0,0) 75%),
      linear-gradient(180deg,#c9762c 0%,#d9943a 30%,#b5502a 60%,#8a3a22 85%,#5d6b33 100%);}
  .header-sheet{position:absolute;left:0;top:0;width:977px;height:160px}

  .brand{position:absolute;left:48px;top:62px;display:flex;align-items:center;gap:16px}
  .brand-name{font-weight:500;font-size:30px;color:var(--maroon);letter-spacing:.5px}
  .brand-mark{width:58px;height:58px;border-radius:50%;background:var(--maroon)}

  .title{position:absolute;left:55px;top:178px;color:var(--white);font-weight:800;font-size:61px;line-height:58px;letter-spacing:-.5px}
  .title-tag{position:absolute;left:58px;top:310px;width:268px;height:35px;background:var(--white);color:#3a1414;font-weight:700;font-size:28px;line-height:35px;letter-spacing:9px;text-align:center}

  .plans{position:absolute;left:62px;top:376px;width:838px;height:640px;border:4px solid var(--white);border-bottom:none;border-radius:22px 22px 0 0;background:#e6e6e6;overflow:hidden}
  .plans-head{display:grid;grid-template-columns:273px 282px 275px;height:138px;background:linear-gradient(90deg,#5e1418,#6e1a1c 50%,#5e1418)}
  .plan-head{text-align:center;color:var(--white);padding-top:22px;border-right:1px solid rgba(255,255,255,.25)}
  .plan-head:last-child{border-right:none}
  .plan-name{font-weight:700;font-size:20px;line-height:22px;padding-bottom:6px;margin:0 58px 8px;border-bottom:1px solid rgba(255,255,255,.6)}
  .plan-sub{font-size:13.5px;line-height:17px}

  .plans-body{display:grid;grid-template-columns:273px 282px 275px;height:500px}
  .plan-col{padding:0 14px;background:#f1f1f1}
  .plan-col:nth-child(2){height:490px}
  .plan-list{background:var(--panel);height:100%;list-style:none}
  .plan-col.featured{background:#f1f1f1}
  .featured .plan-list{background:var(--pink)}
  .plan-list li{display:flex;align-items:flex-start;gap:8px;padding:0 10px 0 18px;font-size:13.5px;line-height:17px;height:38px;align-items:center}
  .plan-list li.tall{height:57px}
  .plan-list li:nth-child(even){background:var(--panel-stripe)}
  .featured .plan-list li:nth-child(even){background:var(--pink-stripe)}
  .plan-list li.lead{display:block;height:132px;text-align:center;padding:14px 8px 0;background:transparent}
  .lead-title{display:block;color:var(--maroon);font-weight:700;font-size:13.5px;margin-top:3px}
  .lead-text{display:block;font-size:14px;line-height:17px}
  .icon{flex:0 0 12px;width:12px;height:12px}
  .lead .icon{display:block;margin:0 auto}

  .badge{position:absolute;left:836px;top:350px;width:84px;height:84px}
  .badge-text{position:absolute;left:848px;top:372px;width:60px;text-align:center;color:var(--white);font-weight:800;font-size:12px;line-height:12px;transform:rotate(-14deg)}

  .footer{position:absolute;left:0;top:1048px;width:977px;height:217px;background:var(--charcoal)}

  .result{position:absolute;top:942px;width:392px;height:160px;border:4px solid var(--white);border-radius:16px;overflow:hidden;display:flex;background:var(--white)}
  .result.before{left:63px}
  .result.after{left:503px;flex-direction:row-reverse}
  .result-label{width:76px;display:flex;align-items:center;justify-content:center;color:var(--white);font-weight:700;font-size:24px;letter-spacing:1px}
  .result-label span{transform:rotate(-90deg);white-space:nowrap}
  .before .result-label{background:#2e2e2e;border-right:4px solid var(--white)}
  .after .result-label{background:var(--maroon);border-left:4px solid var(--white)}
  .result-photo{flex:1;border-radius:12px;background:linear-gradient(180deg,#3f5a2c 0%,#5b8a34 35%,#78b13d 70%,#8cc24a 100%)}

  .contact{position:absolute;left:66px;top:1138px;color:var(--white);font-weight:500;font-size:24px;line-height:30px}
  .contact-row{display:flex;align-items:center;gap:16px}
  .contact-row svg{width:22px;height:22px}
  .web-bar{position:absolute;left:529px;top:1141px;width:460px;height:46px;background:var(--maroon);border:1px solid #c5a0a4;border-right:none;color:var(--white);font-weight:600;font-size:26px;line-height:44px;padding-left:20px}
</style>
</head>
<body>
<main class="flier">
  <div class="hero-photo" role="img" aria-label="Cemetery grounds lined with autumn trees in red and orange foliage"></div>
  <svg class="header-sheet" viewBox="0 0 977 160" aria-hidden="true"><path d="M0 0H618C575 70 525 150 420 155H0Z" fill="#fff"/></svg>

  <div class="brand"><span class="brand-name">Hollowbrook Memorial</span><span class="brand-mark"></span></div>

  <h1 class="title">2024 GRAVESITE<br>LANDSCAPING</h1>
  <div class="title-tag">PACKAGES</div>

  <section class="plans">
    <div class="plans-head">
      <div class="plan-head"><div class="plan-name">Seasonal<br>Care</div><div class="plan-sub">Seasonal landscaping<br>grave care</div></div>
      <div class="plan-head"><div class="plan-name">Basic Care<br>Endowment</div><div class="plan-sub">Landscaping care forever for<br>graves with no plantings.</div></div>
      <div class="plan-head"><div class="plan-name">Perpetual Care<br>Endowment</div><div class="plan-sub">Landscaping care forever for<br>graves with plantings.</div></div>
    </div>
    <div class="plans-body">
      <div class="plan-col">
        <ul class="plan-list">
          <li class="lead"><svg class="icon" viewBox="0 0 12 12"><circle cx="6" cy="6" r="6" fill="#2fb36a"/><path d="M3.2 6.2l1.9 1.8 3.7-3.8" stroke="#fff" stroke-width="1.5" fill="none"/></svg><span class="lead-title">WEEDING &amp; TRIMMING</span><span class="lead-text">Approximately every 7 weeks during the growing season :<br>mid-April through<br>mid-October</span></li>
          <li><svg class="icon" viewBox="0 0 12 12"><circle cx="6" cy="6" r="6" fill="#e0393b"/><path d="M4 4l4 4M8 4l-4 4" stroke="#fff" stroke-width="1.5"/></svg>Monument Leveling</li>
          <li class="tall"><svg class="icon" viewBox="0 0 12 12"><circle cx="6" cy="6" r="6" fill="#e0393b"/><path d="M4 4l4 4M8 4l-4 4" stroke="#fff" stroke-width="1.5"/></svg>Payment ensures grave<br>care forever</li>
          <li><svg class="icon" viewBox="0 0 12 12"><circle cx="6" cy="6" r="6" fill="#e0393b"/><path d="M4 4l4 4M8 4l-4 4" stroke="#fff" stroke-width="1.5"/></svg>Monument Cleaning</li>
          <li><svg class="icon" viewBox="0 0 12 12"><circle cx="6" cy="6" r="6" fill="#e0393b"/><path d="M4 4l4 4M8 4l-4 4" stroke="#fff" stroke-width="1.5"/></svg>Full bed of Boxwood Shrubs</li>
          <li><svg class="icon" viewBox="0 0 12 12"><circle cx="6" cy="6" r="6" fill="#e0393b"/><path d="M4 4l4 4M8 4l-4 4" stroke="#fff" stroke-width="1.5"/></svg>Replacement of Shrubs</li>
          <li><svg class="icon" viewBox="0 0 12 12"><circle cx="6" cy="6" r="6" fill="#e0393b"/><path d="M4 4l4 4M8 4l-4 4" stroke="#fff" stroke-width="1.5"/></svg>Trust Certificate</li>
        </ul>
      </div>
      <div class="plan-col">
        <ul class="plan-list">
          <li class="lead"><svg class="icon" viewBox="0 0 12 12"><circle cx="6" cy="6" r="6" fill="#2fb36a"/><path d="M3.2 6.2l1.9 1.8 3.7-3.8" stroke="#fff" stroke-width="1.5" fill="none"/></svg><span class="lead-title">WEEDING &amp; TRIMMING</span><span class="lead-text">2 times per year :<br>mid-May &amp;<br>mid-September</span></li>
          <li><svg class="icon" viewBox="0 0 12 12"><circle cx="6" cy="6" r="6" fill="#2fb36a"/><path d="M3.2 6.2l1.9 1.8 3.7-3.8" stroke="#fff" stroke-width="1.5" fill="none"/></svg>Monument Leveling</li>
          <li class="tall"><svg class="icon" viewBox="0 0 12 12"><circle cx="6" cy="6" r="6" fill="#2fb36a"/><path d="M3.2 6.2l1.9 1.8 3.7-3.8" stroke="#fff" stroke-width="1.5" fill="none"/></svg>Payment ensures grave<br>care forever</li>
          <li><svg class="icon" viewBox="0 0 12 12"><circle cx="6" cy="6" r="6" fill="#e0393b"/><path d="M4 4l4 4M8 4l-4 4" stroke="#fff" stroke-width="1.5"/></svg>Monument Cleaning</li>
          <li><svg class="icon" viewBox="0 0 12 12"><circle cx="6" cy="6" r="6" fill="#e0393b"/><path d="M4 4l4 4M8 4l-4 4" stroke="#fff" stroke-width="1.5"/></svg>Full bed of Boxwood Shrubs</li>
          <li><svg class="icon" viewBox="0 0 12 12"><circle cx="6" cy="6" r="6" fill="#e0393b"/><path d="M4 4l4 4M8 4l-4 4" stroke="#fff" stroke-width="1.5"/></svg>Replacement of Shrubs</li>
          <li><svg class="icon" viewBox="0 0 12 12"><circle cx="6" cy="6" r="6" fill="#e0393b"/><path d="M4 4l4 4M8 4l-4 4" stroke="#fff" stroke-width="1.5"/></svg>Trust Certificate</li>
        </ul>
      </div>
      <div class="plan-col featured">
        <ul class="plan-list">
          <li class="lead"><svg class="icon" viewBox="0 0 12 12"><circle cx="6" cy="6" r="6" fill="#2fb36a"/><path d="M3.2 6.2l1.9 1.8 3.7-3.8" stroke="#fff" stroke-width="1.5" fill="none"/></svg><span class="lead-title">WEEDING &amp; TRIMMING</span><span class="lead-text">Approximately every 7 weeks during the growing season :<br>mid-April through<br>mid-October</span></li>
          <li><svg class="icon" viewBox="0 0 12 12"><circle cx="6" cy="6" r="6" fill="#2fb36a"/><path d="M3.2 6.2l1.9 1.8 3.7-3.8" stroke="#fff" stroke-width="1.5" fill="none"/></svg>Monument Leveling</li>
          <li class="tall"><svg class="icon" viewBox="0 0 12 12"><circle cx="6" cy="6" r="6" fill="#2fb36a"/><path d="M3.2 6.2l1.9 1.8 3.7-3.8" stroke="#fff" stroke-width="1.5" fill="none"/></svg>Payment ensures grave<br>care forever</li>
          <li><svg class="icon" viewBox="0 0 12 12"><circle cx="6" cy="6" r="6" fill="#2fb36a"/><path d="M3.2 6.2l1.9 1.8 3.7-3.8" stroke="#fff" stroke-width="1.5" fill="none"/></svg>Monument Cleaning</li>
          <li><svg class="icon" viewBox="0 0 12 12"><circle cx="6" cy="6" r="6" fill="#2fb36a"/><path d="M3.2 6.2l1.9 1.8 3.7-3.8" stroke="#fff" stroke-width="1.5" fill="none"/></svg>Full bed of Boxwood Shrubs</li>
          <li><svg class="icon" viewBox="0 0 12 12"><circle cx="6" cy="6" r="6" fill="#2fb36a"/><path d="M3.2 6.2l1.9 1.8 3.7-3.8" stroke="#fff" stroke-width="1.5" fill="none"/></svg>Replacement of Shrubs</li>
          <li><svg class="icon" viewBox="0 0 12 12"><circle cx="6" cy="6" r="6" fill="#2fb36a"/><path d="M3.2 6.2l1.9 1.8 3.7-3.8" stroke="#fff" stroke-width="1.5" fill="none"/></svg>Trust Certificate</li>
        </ul>
      </div>
    </div>
  </section>

  <svg class="badge" viewBox="0 0 84 84" aria-hidden="true">
    <polygon fill="#e01f26" stroke="#fff" stroke-width="2" points="42,2 49,12 61,6 63,19 76,20 71,32 82,40 72,49 78,61 65,63 63,76 51,71 42,82 33,71 21,76 19,63 6,61 12,49 2,40 13,32 8,20 21,19 23,6 35,12"/>
  </svg>
  <div class="badge-text">MOST POPULAR</div>

  <div class="footer"></div>

  <div class="result before">
    <div class="result-label"><span>BEFORE</span></div>
    <div class="result-photo" role="img" aria-label="Overgrown gravesite with untrimmed shrubs before care"></div>
  </div>
  <div class="result after">
    <div class="result-label"><span>AFTER</span></div>
    <div class="result-photo" role="img" aria-label="Neatly trimmed boxwood bed behind a grave marker after care"></div>
  </div>

  <div class="contact">
    <div class="contact-row"><svg viewBox="0 0 24 24" aria-hidden="true"><path fill="#bdbdbd" d="M6.6 10.8a15.1 15.1 0 0 0 6.6 6.6l2.2-2.2c.3-.3.7-.4 1-.2 1.1.4 2.3.6 3.6.6.6 0 1 .4 1 1V20c0 .6-.4 1-1 1A17 17 0 0 1 3 4c0-.6.4-1 1-1h3.5c.6 0 1 .4 1 1 0 1.3.2 2.5.6 3.6.1.3 0 .7-.2 1z"/></svg>(201) 555-0148</div>
    <div class="contact-row"><svg viewBox="0 0 24 24" aria-hidden="true"><rect x="2" y="5" width="20" height="14" rx="1" fill="#bdbdbd"/><path d="M2.5 5.5l9.5 7.5 9.5-7.5" stroke="#363636" stroke-width="1.5" fill="none"/></svg>info@hollowbrookmemorial.org</div>
  </div>
  <div class="web-bar">www.hollowbrookmemorial.org</div>
</main>
</body>
</html>
```